Aerospace Center needs app design

We need a design that would be a creative and innovative look of a simple idea connecting air traffic control situations with sonification.
We would like to see designs that use the elements shown in the short video which are different pads, showing 4 different colors, connecting with a degree and feeling of urgency. The different pads will be movable over screen, similar as to a whiteboard where you can move things around. Each of those pads has 4 different elements that are shown:
- ATC Event (you can chose different setups)
- Select a status (you can chose between Information, Caution and Alert. Color needs to feel more alert from Information to Alert.
- Notes box (you can open the box and write additional text on it)
- Music (you can chose different files. on the right side you can see a small group of notes. When you hover over the notes, music will be played without pressing a play or stop button.
The second video is an overview of music archival program that is connected with the pads.
Look and feel
Each slider illustrates characteristics of the customer's brand and the style your logo design should communicate.

```html
<!DOCTYPE html>
<html lang="en">
<head>
<meta charset="utf-8">
<title>TALO Soundboards</title>
<link href="https://fonts.googleapis.com/css2?family=Mulish:wght@400;600;700;800&display=swap" rel="stylesheet">
<style>
:root{
  --page:#f0f4f8;
  --side:#2a2b3d;
  --side-active:#3c3e52;
  --brand:#0f92d8;
  --white:#ffffff;
  --text:#2b2d3a;
  --field-text:#4a4a4a;
  --field-border:#c9c9c9;
  --btn:#1190da;
  --info-h:#0f94d8; --info-b:#12648f;
  --land-h:#a010d8; --land-b:#7f0aa9;
  --caut-h:#bccc04; --caut-b:#95a300;
  --moon-h:#209b06; --moon-b:#177f03;
  --idle-h:#cc3c0c; --idle-b:#efe5e2;
}
*{box-sizing:border-box;margin:0;padding:0}
html,body{width:1200px;height:544px;overflow:hidden}
body{font-family:'Mulish',sans-serif;background:var(--page);position:relative;color:var(--text)}
.sidebar{position:absolute;left:0;top:0;width:232px;height:544px;background:var(--side)}
.brand{height:126px;background:var(--brand);display:flex;align-items:center;justify-content:center;gap:14px}
.brand-mark{width:22px;height:22px;background:var(--white);border-radius:3px}
.brand-name{color:var(--white);font-weight:800;font-size:30px;letter-spacing:1px}
.nav{list-style:none}
.nav li{height:36px;display:flex;align-items:center;padding-left:72px;gap:10px;color:var(--white);font-size:13px;margin-bottom:23px}
.nav li.active{background:var(--side-active);margin-bottom:18px}
.nav svg{width:13px;height:13px;fill:var(--white)}
.nav li.active svg{fill:var(--brand)}
.search{position:absolute;left:601px;top:19px;width:348px;height:30px;display:flex}
.search-field{flex:1;border:1px solid var(--brand);border-right:none;background:var(--white);font-size:10.5px;padding:0 9px;display:flex;align-items:center;color:var(--text)}
.search-btn{width:37px;background:var(--brand);display:flex;align-items:center;justify-content:center}
.search-btn svg{width:14px;height:14px;fill:none;stroke:var(--white);stroke-width:2.6}
.welcome{position:absolute;left:977px;top:25px;font-size:14.5px;display:flex;align-items:center;gap:10px}
.welcome svg{width:12px;height:13px;fill:var(--text)}
.board{position:absolute;left:253px;top:70px;display:grid;grid-template-columns:repeat(5,175px);column-gap:13px;row-gap:14px}
.pad{height:213px;background:var(--body);box-shadow:0 1px 3px rgba(0,0,0,.18);position:relative}
.pad-head{height:35px;background:var(--head);display:flex;align-items:center;justify-content:space-between;padding:0 8px 0 11px;color:var(--white);font-weight:700;font-size:16px}
.pad-close{width:14px;height:14px;background:var(--white);border-radius:2px;display:flex;align-items:center;justify-content:center}
.pad-close svg{width:8px;height:8px;stroke:var(--head);stroke-width:3}
.field{position:absolute;left:8px;width:159px;height:27px;background:var(--white);border:1px solid var(--field-border);border-radius:2px;font-size:10.5px;color:var(--field-text);display:flex;align-items:center;padding-left:8px}
.select::after{content:"";position:absolute;right:8px;top:12px;border-left:3.5px solid transparent;border-right:3.5px solid transparent;border-top:4px solid #333}
.f1{top:45px}.f2{top:78px}.f3{top:111px}.f4{top:143px}
.play{position:absolute;left:29px;top:175px;width:117px;height:26px;background:var(--btn);border:1px solid rgba(255,255,255,.7);display:flex;align-items:center;justify-content:center}
.play svg{width:13px;height:13px;fill:var(--white)}
.info{--head:var(--info-h);--body:var(--info-b)}
.land{--head:var(--land-h);--body:var(--land-b)}
.caution{--head:var(--caut-h);--body:var(--caut-b)}
.alert{--head:var(--moon-h);--body:var(--moon-b)}
.idle{--head:var(--idle-h);--body:var(--idle-b)}
</style>
</head>
<body>
<aside class="sidebar">
  <div class="brand"><span class="brand-mark"></span><span class="brand-name">TALO</span></div>
  <ul class="nav">
    <li class="active"><svg viewBox="0 0 16 16"><path d="M5 2l10-2v11a2.5 2 0 1 1-2-2V4L7 5v8a2.5 2 0 1 1-2-2z"/></svg>Soundboards</li>
    <li><svg viewBox="0 0 16 16"><path d="M1 3h10v7H4l-3 3zM12 6h3v8l-3-2H6v-1h6z"/></svg>Surveys</li>
    <li><svg viewBox="0 0 16 16"><circle cx="8" cy="2.5" r="2"/><path d="M5 6h5v8h2v2H4v-2h2V8H5z"/></svg>Help</li>
    <li><svg viewBox="0 0 16 16"><path d="M2 0h12v2h-1c0 3-2 4-3.5 6C11 10 13 11 13 14h1v2H2v-2h1c0-3 2-4 3.5-6C5 6 3 5 3 2H2z"/></svg>My first Experiment</li>
    <li><svg viewBox="0 0 16 16"><path d="M3 7h10v9H3zM5 7V5a3 3 0 0 1 6 0v2H9V5a1 1 0 0 0-2 0v2z"/></svg>Log Out</li>
  </ul>
</aside>

<div class="search"><div class="search-field">Search</div><div class="search-btn"><svg viewBox="0 0 16 16"><circle cx="6.5" cy="6.5" r="4.8"/><path d="M10 10l4.5 4.5"/></svg></div></div>
<div class="welcome"><svg viewBox="0 0 12 13"><circle cx="6" cy="3.3" r="3.2"/><path d="M0 13c0-4 2.5-5.5 6-5.5S12 9 12 13z"/></svg>Welcome to Maren T Hale</div>

<main class="board">
  <section class="pad info"><header class="pad-head">SO1<span class="pad-close"><svg viewBox="0 0 8 8"><path d="M1 1l6 6M7 1L1 7"/></svg></span></header>
    <div class="field select f1">Select atc event</div><div class="field select f2">01. Information</div><div class="field f3">Note</div><div class="field select f4">Lark T...</div>
    <div class="play"><svg viewBox="0 0 16 16"><path d="M5 2l10-2v11a2.5 2 0 1 1-2-2V4L7 5v8a2.5 2 0 1 1-2-2z"/></svg></div></section>
  <section class="pad land"><header class="pad-head">SO2<span class="pad-close"><svg viewBox="0 0 8 8"><path d="M1 1l6 6M7 1L1 7"/></svg></span></header>
    <div class="field select f1">Landing</div><div class="field select f2">01. Information</div><div class="field f3">Note</div><div class="field select f4">Lark T...</div>
    <div class="play"><svg viewBox="0 0 16 16"><path d="M5 2l10-2v11a2.5 2 0 1 1-2-2V4L7 5v8a2.5 2 0 1 1-2-2z"/></svg></div></section>
  <section class="pad caution"><header class="pad-head">SO3<span class="pad-close"><svg viewBox="0 0 8 8"><path d="M1 1l6 6M7 1L1 7"/></svg></span></header>
    <div class="field select f1">Depature</div><div class="field select f2">02. Caution</div><div class="field f3">Note</div><div class="field select f4">Harbo...</div>
    <div class="play"><svg viewBox="0 0 16 16"><path d="M5 2l10-2v11a2.5 2 0 1 1-2-2V4L7 5v8a2.5 2 0 1 1-2-2z"/></svg></div></section>
  <section class="pad alert"><header class="pad-head">SO4<span class="pad-close"><svg viewBox="0 0 8 8"><path d="M1 1l6 6M7 1L1 7"/></svg></span></header>
    <div class="field select f1">Moon</div><div class="field select f2">03.Alert</div><div class="field f3">Note</div><div class="field select f4">Glimm...</div>
    <div class="play"><svg viewBox="0 0 16 16"><path d="M5 2l10-2v11a2.5 2 0 1 1-2-2V4L7 5v8a2.5 2 0 1 1-2-2z"/></svg></div></section>
  <section class="pad idle"><header class="pad-head">SO6<span class="pad-close"><svg viewBox="0 0 8 8"><path d="M1 1l6 6M7 1L1 7"/></svg></span></header>
    <div class="field select f1">Select atc event</div><div class="field select f2">Select Status I...</div><div class="field f3">Note</div><div class="field select f4">Select...</div>
    <div class="play"><svg viewBox="0 0 16 16"><path d="M5 2l10-2v11a2.5 2 0 1 1-2-2V4L7 5v8a2.5 2 0 1 1-2-2z"/></svg></div></section>
  <section class="pad idle"><header class="pad-head">SO7<span class="pad-close"><svg viewBox="0 0 8 8"><path d="M1 1l6 6M7 1L1 7"/></svg></span></header>
    <div class="field select f1">Select atc event</div><div class="field select f2">Select Status I...</div><div class="field f3">Note</div><div class="field select f4">Select...</div>
    <div class="play"><svg viewBox="0 0 16 16"><path d="M5 2l10-2v11a2.5 2 0 1 1-2-2V4L7 5v8a2.5 2 0 1 1-2-2z"/></svg></div></section>
  <section class="pad idle"><header class="pad-head">SO8<span class="pad-close"><svg viewBox="0 0 8 8"><path d="M1 1l6 6M7 1L1 7"/></svg></span></header>
    <div class="field select f1">Select atc event</div><div class="field select f2">Select Status I...</div><div class="field f3">Note</div><div class="field select f4">Select...</div>
    <div class="play"><svg viewBox="0 0 16 16"><path d="M5 2l10-2v11a2.5 2 0 1 1-2-2V4L7 5v8a2.5 2 0 1 1-2-2z"/></svg></div></section>
  <section class="pad idle"><header class="pad-head">SO9<span class="pad-close"><svg viewBox="0 0 8 8"><path d="M1 1l6 6M7 1L1 7"/></svg></span></header>
    <div class="field select f1">Select atc event</div><div class="field select f2">Select Status I...</div><div class="field f3">Note</div><div class="field select f4">Select...</div>
    <div class="play"><svg viewBox="0 0 16 16"><path d="M5 2l10-2v11a2.5 2 0 1 1-2-2V4L7 5v8a2.5 2 0 1 1-2-2z"/></svg></div></section>
  <section class="pad idle"><header class="pad-head">SO10<span class="pad-close"><svg viewBox="0 0 8 8"><path d="M1 1l6 6M7 1L1 7"/></svg></span></header>
    <div class="field select f1">Select atc event</div><div class="field select f2">Select Status I...</div><div class="field f3">Note</div><div class="field select f4">Select...</div>
    <div class="play"><svg viewBox="0 0 16 16"><path d="M5 2l10-2v11a2.5 2 0 1 1-2-2V4L7 5v8a2.5 2 0 1 1-2-2z"/></svg></div></section>
  <section class="pad idle"><header class="pad-head">SO5<span class="pad-close"><svg viewBox="0 0 8 8"><path d="M1 1l6 6M7 1L1 7"/></svg></span></header>
    <div class="field select f1">Select atc event</div><div class="field select f2">Select Status I...</div><div class="field f3">Note</div><div class="field select f4">Select...</div>
    <div class="play"><svg viewBox="0 0 16 16"><path d="M5 2l10-2v11a2.5 2 0 1 1-2-2V4L7 5v8a2.5 2 0 1 1-2-2z"/></svg></div></section>
</main>
</body>
</html>
```